NEW Wordpress Website Design for a Dynamic Long Term Healthcare Company in Hawaii

I would like a new website design for my current company, Marlow Health Collective, which has two different brands - Marlow Homecare and Marlow Senior Living. You can see the current website at www.marlowhealth-example.com. The website should be built using Wordpress Software and the Framewise theme. The website should have a local Hawaii island/tropical feel, but look professional for healthcare. I'm looking for something fresh, and want the designer to select colors, styles, etc.

In the Header, on all pages, I would like a menu that includes Home Care, Senior Living, Rates, and About Us.
Under each of the Header Menu Titles, I would like these drop downs included:
Home Care (drop down pages)- Nurse Aide Care, 24-Hour Home Care, Skilled Nursing, Lifestyle Aide, Hospice at Home, Bathing & Meal Service.
Senior Living (drop down pages) - Long-Term Stay, Short-Term Stay.
Rates (drop down page) - Rates.
About Us (drop down pages) - Our Mission, Ohana Talk, About Dana Marlow.

In the footer, on all pages, you should include the address: 248 Pueo Lane, Suite 310, Honolulu, HI 96817. Phone number: 808-555-0172
The footer should also include buttons for a page called Learn, Caregiver Jobs, and each of the service page links to include: Nurse Aide Care, 24-Hour Home Care, Skilled Nursing, Lifestyle Aide, Hospice at Home, Bathing & Meal Service.
Please don't take the current website and redesign a few aspects. I'm looking for a completely different look and feel.

Target Market(s)

40-80 year olds

Industry/Entity Type

Long Term Healthcare

Coding

Coded - Design and coding required

Requirements
Should not have
• Our existing website as a template. We are looking for a complete redesign. Thank you.

```html
<!DOCTYPE html>
<html lang="en">
<head>
<meta charset="utf-8">
<title>Marlow Health Collective — Homecare &amp; Senior Living</title>
<link rel="stylesheet" href="https://fonts.googleapis.com/css2?family=Lora:wght@400;500&family=Montserrat:wght@400;500;600;700&display=swap">
<style>
:root{
  --orange:#ee7d1a;
  --orange-deep:#d9600f;
  --red:#c8371d;
  --ink:#1f1b18;
  --text:#4a4440;
  --sand:#f6d7a8;
  --white:#ffffff;
  --line:#d8d2cc;
}
*{box-sizing:border-box;margin:0;padding:0}
html,body{width:1200px;height:4307px;overflow:hidden}
body{position:relative;background:var(--white);font-family:"Montserrat",sans-serif;color:var(--text)}
.abs{position:absolute}
.serif{font-family:"Lora",serif;color:var(--ink);font-weight:400}
.eyebrow{font-size:13px;font-weight:600;letter-spacing:1.5px;color:var(--red);text-transform:uppercase}
.btn{position:absolute;display:flex;align-items:center;justify-content:center;gap:6px;border-radius:30px;font-size:13px;font-weight:600;letter-spacing:.5px;text-transform:uppercase}
.btn-fill{background:linear-gradient(90deg,var(--orange-deep),var(--orange));color:var(--white)}
.btn-line{border:2px solid var(--orange-deep);color:var(--orange-deep);background:var(--white)}
.photo{position:absolute}
.brand{display:flex;align-items:center;gap:10px;font-weight:700;color:var(--orange-deep)}
.brand-mark{width:30px;height:30px;border-radius:50%;background:var(--orange-deep);flex:none}

/* header */
.site-header{position:absolute;left:0;top:0;width:1200px;height:90px;z-index:5}
.site-header .brand{position:absolute;left:100px;top:26px;font-size:19px;width:260px;line-height:1.15}
.nav{position:absolute;left:390px;top:34px;display:flex;gap:36px;font-size:13px;font-weight:500;color:var(--ink)}
.nav span::after{content:" ⌄";color:#999}
.header-cta{left:920px;top:24px;width:132px;height:38px;font-size:12px}

/* hero */
.hero{position:absolute;left:0;top:0;width:1200px;height:735px;background:linear-gradient(100deg,#fff4dc 0%,#ffe7bd 45%,#f9d9a2 100%);overflow:hidden}
.hero-photo{right:0;top:120px;width:700px;height:600px;background:radial-gradient(ellipse at 45% 40%,#3a8fd0 0%,#58b3d8 18%,rgba(88,179,216,0) 40%),linear-gradient(160deg,#f3e2c4 0%,#d9b68a 45%,#8a5c3c 100%)}
.hero-fade{position:absolute;left:470px;top:0;width:280px;height:735px;background:linear-gradient(90deg,#ffedca,rgba(255,237,202,0))}
.hero .eyebrow{left:120px;top:206px;font-size:20px;font-weight:500;letter-spacing:1px}
.hero h1{position:absolute;left:120px;top:228px;font-size:70px;line-height:68px}
.hero p{position:absolute;left:124px;top:388px;width:380px;font-size:17px;line-height:29px}
.hero-dots{position:absolute;left:34px;top:326px;display:flex;flex-direction:column;gap:14px}
.hero-dots i{width:11px;height:11px;border-radius:50%;background:#e6c9a0;display:block}
.hero-dots i:first-child{background:var(--orange-deep)}

/* about */
.about-photo{left:103px;top:808px;width:454px;height:454px;border-radius:50%;background:radial-gradient(circle at 50% 60%,#c9b39a 0%,#a99a86 18%,rgba(169,154,134,0) 40%),linear-gradient(180deg,#5f8f3e,#8cbc62 50%,#9a9a8c)}
.about-ring{left:88px;top:793px;width:484px;height:484px;border-radius:50%;border:8px solid var(--sand)}
.about .eyebrow{left:615px;top:824px}
.about h2{position:absolute;left:608px;top:840px;font-size:58px;line-height:54px}
.about p{position:absolute;left:614px;top:990px;width:520px;font-size:16.5px;line-height:29.5px}

/* home care */
.homecare{position:absolute;left:0;top:1320px;width:1200px;height:640px;background:linear-gradient(90deg,#fff7e6,#fde6c1);overflow:hidden}
.homecare-photo{right:0;top:48px;width:640px;height:600px;background:radial-gradient(ellipse at 55% 30%,#b2303e 0%,rgba(178,48,62,0) 22%),linear-gradient(160deg,#e4e7b8 0%,#cdd6a2 35%,#7b4a2e 70%,#d8c7a4 100%)}
.homecare-fade{position:absolute;left:520px;top:0;width:160px;height:640px;background:linear-gradient(90deg,#fff3de,rgba(255,243,222,0))}
.homecare .eyebrow{left:114px;top:114px}
.homecare h2{position:absolute;left:114px;top:126px;font-size:56px}
.homecare p{position:absolute;left:114px;top:215px;width:420px;font-size:15px;line-height:23.5px;color:var(--ink)}
.service-list{position:absolute;left:120px;top:310px;display:grid;grid-template-columns:225px 220px;row-gap:16px;font-size:15.5px;font-weight:500;color:var(--ink)}
.service-list li{list-style:none;display:flex;align-items:center;gap:12px}
.chev{width:8px;height:12px}

/* senior living */
.senior{position:absolute;left:0;top:1945px;width:1200px;height:652px;background:linear-gradient(120deg,#e46a14 0%,#f29225 55%,#f5a534 100%);color:var(--white);text-align:center}
.senior .eyebrow{position:absolute;left:0;width:1200px;top:70px;color:var(--white)}
.senior h2{position:absolute;left:0;width:1200px;top:86px;font-size:52px;color:var(--white)}
.senior p{position:absolute;left:240px;width:720px;top:170px;font-size:17px;line-height:27px}
.stay-card{position:absolute;top:255px;width:453px;height:295px;border-radius:0 0 40px 0;overflow:hidden}
.stay-card .photo{inset:0}
.stay-card h3{position:absolute;left:0;right:0;bottom:36px;font-size:23px;font-weight:700;letter-spacing:.5px}
.stay-card h3::after{content:"";display:block;width:40px;height:2px;background:var(--white);margin:10px auto 0}

/* blogs */
.blogs h2{position:absolute;left:114px;top:2630px;font-size:50px}
.blog-feature{left:115px;top:2761px;width:505px;height:400px;background:radial-gradient(ellipse at 40% 45%,#3f7fb6 0%,rgba(63,127,182,0) 25%),linear-gradient(160deg,#d8863a,#8a5a3c 50%,#2e2623)}
.blog-feature .meta{position:absolute;left:36px;top:285px}
.blog-feature h3{position:absolute;left:36px;top:318px;width:420px;font-size:17px;line-height:27px;font-weight:600;color:var(--white)}
.date{display:inline-flex;align-items:center;gap:6px;background:var(--orange-deep);color:var(--white);font-size:11px;font-weight:700;padding:4px 8px;border-radius:2px}
.blog-card{position:absolute;left:633px;width:466px;height:192px;border:1px solid var(--line);background:var(--white)}
.blog-card .photo{left:0;top:0;width:225px;height:190px}
.blog-card .body{position:absolute;left:248px;top:23px;width:200px}
.blog-card h4{font-size:11.5px;line-height:15px;font-weight:700;color:var(--ink);margin:9px 0 6px}
.blog-card p{font-size:10.5px;line-height:15px;color:#777}
.blog-card a{display:inline-block;margin-top:5px;font-size:9.5px;font-weight:600;color:var(--orange-deep);text-decoration:underline}

/* contact */
.contact{position:absolute;left:0;top:3240px;width:1200px;height:630px;background:linear-gradient(180deg,#fff 0%,#fff6e4 60%,#fde0ae 100%);overflow:hidden}
.contact .eyebrow{left:104px;top:78px;font-size:11px;letter-spacing:.5px}
.contact h2{position:absolute;left:104px;top:96px;font-size:41px;line-height:42px}
.field{position:absolute;height:43px;border:1px solid var(--line);background:var(--white);font-size:13px;color:#666;padding:13px 20px}
.contact-photo{left:650px;top:100px;width:458px;height:458px;border-radius:50%;background:radial-gradient(ellipse at 55% 55%,#c9302c 0%,rgba(201,48,44,0) 18%),radial-gradient(ellipse at 75% 50%,#2f7fc4 0%,rgba(47,127,196,0) 16%),linear-gradient(180deg,#8a4a22 0%,#e8d79a 30%,#c9a46c 65%,#7a5a42 100%);box-shadow:0 0 0 10px var(--white),0 0 0 22px var(--orange)}
.contact-band{position:absolute;left:0;bottom:0;width:1200px;height:80px}

/* footer */
.footer{position:absolute;left:0;top:3870px;width:1200px;height:437px;background:var(--white)}
.footer .brand{position:absolute;left:130px;top:70px;width:170px;font-size:20px;line-height:1.2;flex-direction:column;text-align:center;gap:8px}
.foot-btn{position:absolute;left:130px;width:168px;height:34px;font-size:11px;font-weight:600;display:flex;align-items:center;justify-content:center;border-radius:2px;text-transform:uppercase}
.foot-col{position:absolute;top:0;height:370px;border-left:1px solid var(--line)}
.foot-col h5{font-family:"Lora",serif;font-weight:400;font-size:21px;color:var(--ink);margin:60px 0 14px -1px;padding-left:22px;border-left:3px solid var(--orange)}
.foot-col ul{list-style:none;padding-left:24px}
.foot-col li{font-size:12.5px;line-height:31px;color:var(--text)}
.foot-col li::before{content:"› ";color:#aaa}
.contact-line{display:flex;gap:12px;padding-left:22px;margin-bottom:16px;font-size:13px;line-height:18px;color:var(--ink)}
.contact-line svg{flex:none}
.socials{display:flex;gap:9px;padding-left:28px;margin-top:8px}
.socials span{width:30px;height:30px;border-radius:50%;background:var(--orange-deep)}
.copyright{position:absolute;left:0;top:4240px;width:1200px;border-top:1px solid var(--line);text-align:center;padding-top:27px;font-size:11.5px;color:var(--ink)}
.copyright u{color:var(--orange-deep)}
</style>
</head>
<body>

<section class="hero">
  <div class="photo hero-photo" role="img" aria-label="Caregiver in blue scrubs sitting with a smiling senior woman on a sofa in a bright living room"></div>
  <div class="hero-fade"></div>
  <svg class="abs" style="left:0;top:560px" width="1200" height="180" viewBox="0 0 1200 180" aria-hidden="true">
    <path d="M0 30 C200 150 520 150 780 130 C960 115 1100 90 1200 60 L1200 180 L0 180 Z" fill="#fff"/>
    <path d="M0 30 C200 150 520 150 780 130 C960 115 1100 90 1200 60 L1200 82 C1100 110 960 138 780 150 C520 168 200 165 0 60 Z" fill="#e0651a"/>
  </svg>
  <div class="hero-dots"><i></i><i></i><i></i></div>
  <div class="abs eyebrow">Marlow Health Collective</div>
  <h1 class="serif">Homecare &amp;<br>Senior Living</h1>
  <p>Marlow Homecare provides a variety of professional in-home health care services.</p>
  <a class="btn btn-fill" style="left:120px;top:473px;width:176px;height:46px">View Rates ›</a>
  <a class="btn btn-line" style="left:311px;top:473px;width:174px;height:46px">Contact Us ›</a>
</section>

<header class="site-header">
  <div class="brand"><span class="brand-mark"></span><span>Marlow Health Collective</span></div>
  <nav class="nav"><span>HOME CARE</span><span>SENIOR LIVING</span><span>RATES</span><span>ABOUT US</span></nav>
  <a class="btn btn-fill header-cta">Contact Us</a>
</header>

<section class="about">
  <div class="abs about-ring" aria-hidden="true"></div>
  <div class="photo about-photo" role="img" aria-label="Caregiver helping a woman with a walker along a garden path"></div>
  <div class="abs eyebrow">Our Mission</div>
  <h2 class="serif">About Marlow<br>Health Collective</h2>
  <p>At Marlow Health Collective, our mission is to provide compassionate and professional long-term healthcare services that empower individuals to maintain their highest level of independence, health, and well-being in the comfort of their own homes or ours, either through our licensed home healthcare agency</p>
  <a class="btn btn-line" style="left:617px;top:1193px;width:174px;height:47px">Learn More ›</a>
</section>

<section class="homecare">
  <div class="photo homecare-photo" role="img" aria-label="Nurse serving a meal to a senior couple at a dining table"></div>
  <div class="homecare-fade"></div>
  <svg class="abs" style="left:0;top:0" width="1200" height="80" viewBox="0 0 1200 80" aria-hidden="true">
    <path d="M0 0 L1200 0 L1200 80 C1100 40 900 10 700 8 C400 6 200 30 0 20 Z" fill="#fff"/>
    <path d="M700 8 C900 10 1100 40 1200 80 L1200 60 C1100 26 900 0 700 0 Z" fill="#e0651a"/>
  </svg>
  <div class="abs eyebrow">Homecare Service</div>
  <h2 class="serif">Home Care</h2>
  <p>Marlow Homecare understands that every person's care journey is unique. We tailor our in-home services to meet the diverse nurturing experience</p>
  <ul class="service-list">
    <li><svg class="chev" viewBox="0 0 8 12"><path d="M1 1l5 5-5 5" stroke="#e0651a" stroke-width="2.5" fill="none"/></svg>Nurse Aide Care</li>
    <li><svg class="chev" viewBox="0 0 8 12"><path d="M1 1l5 5-5 5" stroke="#e0651a" stroke-width="2.5" fill="none"/></svg>Lifestyle Aide</li>
    <li><svg class="chev" viewBox="0 0 8 12"><path d="M1 1l5 5-5 5" stroke="#e0651a" stroke-width="2.5" fill="none"/></svg>24-Hour Home Care</li>
    <li><svg class="chev" viewBox="0 0 8 12"><path d="M1 1l5 5-5 5" stroke="#e0651a" stroke-width="2.5" fill="none"/></svg>Hospice at Home</li>
    <li><svg class="chev" viewBox="0 0 8 12"><path d="M1 1l5 5-5 5" stroke="#e0651a" stroke-width="2.5" fill="none"/></svg>Skilled Nursing</li>
    <li><svg class="chev" viewBox="0 0 8 12"><path d="M1 1l5 5-5 5" stroke="#e0651a" stroke-width="2.5" fill="none"/></svg>Bathing &amp; Meal Service</li>
  </ul>
  <a class="btn btn-fill" style="left:110px;top:457px;width:185px;height:47px">Learn More ›</a>
</section>

<section class="senior">
  <svg class="abs" style="left:0;top:-30px" width="1200" height="60" viewBox="0 0 1200 60" aria-hidden="true"><path d="M0 0 C300 60 700 60 1200 30 L1200 60 L0 60 Z" fill="#e46a14"/></svg>
  <div class="eyebrow">Senior Living Service</div>
  <h2 class="serif">Senior Living</h2>
  <p>Marlow Senior Living creates a warm, supportive, and enriching care home environment where seniors can thrive in their golden years.</p>
  <div class="stay-card" style="left:148px">
    <div class="photo" role="img" aria-label="Senior women knitting together on a sofa by bright windows" style="background:radial-gradient(ellipse at 55% 55%,#b0407e 0%,rgba(176,64,126,0) 25%),linear-gradient(180deg,#eef0c8 0%,#d9d59a 35%,#a07248 70%,#4a3326 100%)"></div>
    <h3>LONG-TERM STAY</h3>
  </div>
  <div class="stay-card" style="left:630px">
    <div class="photo" role="img" aria-label="Caregiver helping a senior man in a bright room" style="background:radial-gradient(ellipse at 55% 45%,#34a6c4 0%,rgba(52,166,196,0) 22%),linear-gradient(180deg,#f1ecc7 0%,#e2d7a8 40%,#9c8468 75%,#5f4a3a 100%)"></div>
    <h3>SHORT-TERM STAY</h3>
  </div>
</section>

<section class="blogs">
  <h2 class="serif">Latest Blogs</h2>
  <article class="photo blog-feature" role="img" aria-label="Caregiver pouring coffee for seniors at a café table">
    <div class="meta"><span class="date">◷ 15 SEP 2024</span></div>
    <h3>Intentional Misuse of Social Media App May Lead to Developer Liability</h3>
  </article>
  <article class="blog-card" style="top:2761px">
    <div class="photo" role="img" aria-label="Seniors gathered at an outdoor garden table" style="background:linear-gradient(160deg,#5f8a3e,#a7bf7e 40%,#c9b596 70%,#5e4c3e)"></div>
    <div class="body">
      <span class="date">◷ 04 SEP 2024</span>
      <h4>Lorem ipsum dolor sit amet consectetur adipiscing elit</h4>
      <p>Duis aute irure dolor in reprehenderit in voluptate velit esse cillum dolore eu fugiat nulla</p>
      <a>LEARN MORE</a>
    </div>
  </article>
  <article class="blog-card" style="top:2967px">
    <div class="photo" role="img" aria-label="Portrait of a smiling caregiver" style="background:linear-gradient(90deg,#f4efea 0%,#e6d8cc 35%,#b9876a 60%,#3a2520 100%)"></div>
    <div class="body">
      <span class="date">◷ 01 SEP 2024</span>
      <h4>Lorem ipsum dolor sit amet consectetur adipiscing elit</h4>
      <p>Duis aute irure dolor in reprehenderit in voluptate velit esse cillum dolore eu fugiat nulla</p>
      <a>LEARN MORE</a>
    </div>
  </article>
</section>

<section class="contact">
  <div class="abs eyebrow">Contact Marlow Homecare</div>
  <h2 class="serif">Schedule a Complimentary<br>Care Consultation</h2>
  <div class="field" style="left:108px;top:212px;width:237px">First Name</div>
  <div class="field" style="left:350px;top:212px;width:242px">Last Name</div>
  <div class="field" style="left:108px;top:267px;width:237px">Email address</div>
  <div class="field" style="left:350px;top:267px;width:242px">Phone Number</div>
  <div class="field" style="left:108px;top:322px;width:484px;height:103px">Message</div>
  <a class="btn btn-fill" style="left:110px;top:433px;width:196px;height:46px">Send Message ›</a>
  <div class="photo contact-photo" role="img" aria-label="Trainer leading seniors in a seated hand-weight exercise class"></div>
  <svg class="contact-band" viewBox="0 0 1200 80" aria-hidden="true">
    <path d="M0 10 C300 70 700 60 1200 10 L1200 80 L0 80 Z" fill="#fff"/>
    <path d="M0 10 C300 70 700 60 1200 10 L1200 24 C700 76 300 84 0 26 Z" fill="#e0651a"/>
  </svg>
</section>

<footer class="footer">
  <div class="brand"><span class="brand-mark" style="width:44px;height:44px"></span><span>Marlow Health Collective</span></div>
  <a class="foot-btn" style="top:205px;border:1px solid var(--orange-deep);color:var(--orange-deep)">Learn</a>
  <a class="foot-btn" style="top:250px;background:var(--orange-deep);color:var(--white)">Caregiver Jobs</a>
  <div class="foot-col" style="left:365px;width:208px">
    <h5>Navigation</h5>
    <ul><li>Home Care</li><li>Senior Living</li><li>Rates</li><li>About Us</li></ul>
  </div>
  <div class="foot-col" style="left:573px;width:232px">
    <h5>Services</h5>
    <ul><li>Nurse Aide Care</li><li>24-Hour Home Care</li><li>Skilled Nursing</li><li>Lifestyle Aide</li><li>Hospice at Home</li><li>Bathing &amp; Meal Service</li></ul>
  </div>
  <div class="foot-col" style="left:805px;width:300px">
    <h5>Contact Us</h5>
    <div class="contact-line">
      <svg width="22" height="26" viewBox="0 0 22 26"><path d="M11 1C5.5 1 2 5 2 10c0 6 9 15 9 15s9-9 9-15c0-5-3.5-9-9-9z" fill="#e0651a"/><circle cx="11" cy="10" r="3.5" fill="#fff"/></svg>
      <span>248 Pueo Lane, Suite 310,<br>Honolulu, HI 96817</span>
    </div>
    <div class="contact-line">
      <svg width="24" height="24" viewBox="0 0 24 24"><circle cx="12" cy="12" r="12" fill="#e0651a"/><path d="M8 6l2.5 0 1 3-1.5 1.2c.8 1.8 2 3 3.8 3.8L15 12.5l3 1V16c0 .8-.7 1.5-1.5 1.4C11 17 7 13 6.6 7.5 6.5 6.7 7.2 6 8 6z" fill="#fff"/></svg>
      <span>Phone number<br><b style="font-size:15px">808-555-0172</b></span>
    </div>
    <div class="socials"><span role="img" aria-label="Social profile link"></span><span role="img" aria-label="Social profile link"></span><span role="img" aria-label="Video channel link"></span><span role="img" aria-label="Photo profile link"></span></div>
  </div>
</footer>
<div class="copyright">Copyright © 2024 <u>Marlow Health Collective</u>. All Right Reserved</div>

</body>
</html>
```